Commercial Auto Insurance Application and Commercial Property Insurance Application

Hi I need a fillable application for my business to send to potential clients for Commercial Auto Insurance and Commercial Property Insurance. I have attached an example application I currently use for another line of insurance.
Commercial Auto Insurance Application
On the first page I would need the following:
- Business Name: (fill in area for text)
- Effective Date: (fill in area for text)
- How do you structure your business? (Check box for “Sole Proprietor”, “Partnership”, “Corporation”, “LLC”)
- Contact Name: (fill in area for text) / Phone Number: (fill in area for text) / Contact Email (fill in area for text)
- Mailing address: (fill in area for text)
- Garaging location: (fill in area for text)
- Owner Name: (fill in area for text)
- Description of Operations: (fill in area for text)
- How long has the operation been in business? (fill in area for text)
- How many years of experience does your management have in the truck/transportation industry? (fill in area for text)
Coverages
Liability Combined Single Limit: ($1,000,000 (checkbox) / $500,000 (checkbox / $300,000 (checkbox) / Other: (fill in area for text)
Uninsured Motorist CSL: (fill in area for text) (checkbox for “Rejected”)
Medical Payments: (fill in area for text)
Physical Damage: (fill in area for text) (checkbox for Rejected)
Liability Deducible: ($500 checkbox, $1,000 checkbox, $2,500 checkbox, $5,000 checkbox)
Physical Damage Deductible: ($500 checkbox, $1,000 checkbox, $2,500 checkbox, $5,000 checkbox)
Driving radius: (fill in area for text)
How many years have you had your own continuous commercial auto insurance coverage for the current business name? (fill in area for text)
Do any of your vehicles travel across state lines? Yes (checkbox)/ No (checkbox)
If yes, please list all states in which vehicles operate: (fill in area for text)
What is the maximum radius traveled for your customer's business?
0-25 miles (checkbox)
26-50 miles (checkbox)
51-75 miles (checkbox)
76-100 miles (checkbox)
101-150 miles (checkbox)
151-200 miles (checkbox)
201-300 miles (checkbox)
300+ miles (checkbox)
Would you like physical damage coverage for this vehicle? (should be for each vehicle listed)
On the 2nd page of the application I would need the following:
I would need to have it where people can fill in the vehicle information such as VIN:, Year:, Make:, Model:, Type of Vehicle:, Trailers:, Value:
I would also need to have it where people can fill in the drivers with their driver info including Name:, DOB:, DL #:, DL State:, Class of License:, Married: Yes/No, Number of years driving similar vehicle:
Please make it where you can fill in 20 vehicle's information and 20 driver's info.
For the 2nd Application I would need one for Property Insurance
On the Commercial Property Application I would need the following:
- Building Address: (fill in area for text)
- Building Description: (fill in area for text)
- Building Amount: $(fill in area for text)
- Business Personal Property Amount: $ (fill in area for text) (checkbox for Not Needed)
- Building Sq Ft: (fill in area for text)
- Total Area Sq Ft: (fill in area for text)
- Building Construction Type: Wood Frame (checkbox), Steel (checkbox), Fire Resistive (checkbox), Non-Combustible (checkbox), Other (fill in area for text)
- # of stories: (fill in area for text)
- Year Built: (fill in area for text)
- Wiring improvement year: (fill in area for text)
- Roofing improvement year: (fill in area for text)
- Plumbing improvement year: (fill in area for text)
- Heating improvement year: (fill in area for text)
- What is to the right of the building and distance: (fill in area for text)
- What is to the left of the building and distance: (fill in area for text)
- What is in front of the building and distance: (fill in area for text)
- What is behind the building and distance: (fill in area for text)
- Burglar alarm installation and serviced by: (fill in area for text) None (checkbox)
- Does the premises have fire protection? Sprinkler system (checkbox), Fire detection (checkbox), Other: (fill in area for text) None (checkbox)

```html
<!DOCTYPE html>
<html lang="en">
<head>
<meta charset="utf-8">
<title>Insurance Application Forms</title>
<link href="https://fonts.googleapis.com/css2?family=Montserrat:wght@400;500;600;700;800&display=swap" rel="stylesheet">
<style>
:root{
  --navy:#0b2b8f;
  --green:#0e9b2c;
  --field:#f2f3f5;
  --field-line:#dcdfe4;
  --ink:#1d1f24;
  --muted:#8a8f98;
  --row-green:#e8f4e9;
  --row-blue:#dde1ec;
  --paper:#ffffff;
  --canvas:#ffffff;
}
*{box-sizing:border-box;margin:0;padding:0}
html,body{width:1200px;height:580px;overflow:hidden;background:var(--canvas);font-family:"Montserrat",sans-serif;color:var(--ink)}
.page{position:absolute;top:64px;width:687px;height:970px;background:var(--paper);transform:scale(.469);transform-origin:top left;box-shadow:0 6px 22px rgba(0,0,0,.22)}
.page-auto{left:70px}.page-vehicles{left:443px}.page-property{left:815px}
.abs{position:absolute}
/* header */
.brand{position:absolute;left:40px;top:40px;color:var(--navy);font-weight:700;font-size:33px;letter-spacing:1px;line-height:1}
.brand small{display:block;font-size:13px;letter-spacing:6.2px;margin-top:8px}
.brand-mark{display:inline-block;width:14px;height:14px;background:var(--green);margin-right:8px;vertical-align:4px}
.divider{position:absolute;left:492px;top:22px;width:3px;height:80px;background:var(--green)}
.contact{position:absolute;left:508px;top:29px;font-size:9px;line-height:1;color:var(--ink)}
.contact p{position:relative;padding-left:16px;margin-bottom:6px}
.contact p.gap{margin-bottom:10px}
.contact svg{position:absolute;left:0;top:-1px;width:10px;height:11px;fill:var(--navy)}
/* bands */
.band{position:absolute;left:40px;width:608px;height:31px;background:var(--navy);color:#fff;font-weight:700;font-size:13px;display:flex;align-items:center;justify-content:center;letter-spacing:.2px}
.bar{position:absolute;height:22px;background:var(--green);color:#fff;font-size:8px;display:flex;align-items:center;padding-left:15px;font-weight:500}
.label{position:absolute;font-size:8px;color:var(--ink);white-space:nowrap}
.field{position:absolute;height:23px;background:var(--field);border:1px solid var(--field-line);font-size:7px;color:var(--muted);padding:0 15px;display:flex;align-items:center}
.field.tall{align-items:flex-start;padding-top:10px}
.select{justify-content:space-between;color:var(--ink);background:#fff}
.select svg{width:9px;height:6px;stroke:var(--ink);fill:none;stroke-width:1.5}
.check{position:absolute;font-size:6.5px;color:#555;display:flex;align-items:center;gap:6px;white-space:nowrap}
.check::before{content:"";width:10px;height:10px;border:1px solid #555;background:#fff;flex:none}
.caption{position:absolute;left:40px;width:608px;text-align:center;font-size:10px;font-weight:500}
/* tables */
.table{position:absolute;left:40px;width:605px}
.thead{height:22px;background:var(--green);color:#fff;font-size:7.5px;font-weight:600;display:grid;align-items:center;text-align:center}
.vehicles .thead{grid-template-columns:.6fr 1fr 1fr 1fr 1.4fr 1fr 1fr}
.drivers .thead{grid-template-columns:.75fr 1fr 1fr 1fr 1.4fr 1fr 1.5fr;line-height:1.05}
.tr{height:16.9px;background:var(--row-green);position:relative}
.tr:nth-child(odd){background:var(--row-blue)}
.tr .yes{left:434px;top:4px}.tr .no{left:463px;top:4px}
.tr .check{font-size:6.5px}
.tr .check::before{width:8px;height:8px}
</style>
</head>
<body>

<!-- Page 1: commercial auto -->
<section class="page page-auto">
  <div class="brand"><span class="brand-mark"></span>RIDGEWAY<small>INSURANCE SERVICES</small></div>
  <div class="divider"></div>
  <div class="contact">
    <p><svg viewBox="0 0 10 12"><path d="M5 0a4 4 0 0 0-4 4c0 3 4 8 4 8s4-5 4-8a4 4 0 0 0-4-4zm0 5.6A1.6 1.6 0 1 1 5 2.4a1.6 1.6 0 0 1 0 3.2z"/></svg>Ridgeway Insurance Services</p>
    <p>4820 Maple Crest Ave Suite 110</p>
    <p class="gap">Riverton, CA 90817</p>
    <p><svg viewBox="0 0 12 12"><path d="M1 4c0-2 2-3 5-3s5 1 5 3l-2 1-1-2H4L3 5zM2.5 6h7l1 5h-9z"/></svg>Tel: (555) 310-2290</p>
  </div>

  <div class="band" style="top:121px">COMMERCIAL AUTO INSURANCE APPLICATION</div>
  <div class="label" style="left:40px;top:165px">Business Name</div>
  <div class="field" style="left:40px;top:179px;width:300px">Enter Your Text Here</div>
  <div class="label" style="left:352px;top:165px">Effective Date</div>
  <div class="field" style="left:352px;top:179px;width:296px">Enter Your Text Here</div>

  <div class="bar" style="left:40px;top:212px;width:604px">How do you structure your business?</div>
  <div class="check" style="left:60px;top:240px">Sole Proprietor</div>
  <div class="check" style="left:138px;top:240px">Partnership</div>
  <div class="check" style="left:206px;top:240px">Corporation</div>
  <div class="check" style="left:274px;top:240px">LLC</div>

  <div class="label" style="left:40px;top:268px">Contact Name / Phone Number / Contact Email</div>
  <div class="label" style="left:248px;top:268px">Mailing address</div>
  <div class="label" style="left:452px;top:268px">Garaging location</div>
  <div class="field" style="left:40px;top:282px;width:196px">Enter Your Text Here</div>
  <div class="field" style="left:247px;top:282px;width:195px">Enter Your Text Here</div>
  <div class="field" style="left:452px;top:282px;width:196px">Enter Your Text Here</div>

  <div class="label" style="left:40px;top:322px">Owner Name</div>
  <div class="label" style="left:248px;top:322px">Description of Operations</div>
  <div class="label" style="left:452px;top:322px">How long has the operation been in business?</div>
  <div class="field" style="left:40px;top:336px;width:196px">Enter Your Text Here</div>
  <div class="field" style="left:247px;top:336px;width:195px">Enter Your Text Here</div>
  <div class="field" style="left:452px;top:336px;width:196px">Enter Your Text Here</div>

  <div class="label" style="left:42px;top:378px">How many years of experience does your management have in the truck/transportation industry?</div>
  <div class="field" style="left:43px;top:392px;width:601px">Enter Your Text Here</div>

  <div class="band" style="top:432px">COVERAGES</div>
  <div class="label" style="left:352px;top:472px">Uninsured Motorist CSL</div>
  <div class="bar" style="left:40px;top:489px;width:300px">Liability Combined Single Limit</div>
  <div class="field" style="left:352px;top:489px;width:296px">Enter Your Text Here</div>
  <div class="check" style="left:58px;top:523px">$1,000,000</div>
  <div class="check" style="left:135px;top:523px">$500,000</div>
  <div class="check" style="left:208px;top:523px">$300,000</div>
  <div class="check" style="left:282px;top:523px">Other</div>
  <div class="check" style="left:369px;top:520px">Rejected</div>

  <div class="label" style="left:40px;top:547px">Medical Payments</div>
  <div class="field" style="left:40px;top:561px;width:608px">Enter Your Text Here</div>

  <div class="field" style="left:40px;top:602px;width:196px">Physical Damage</div>
  <div class="bar" style="left:247px;top:602px;width:196px">Liability Deductible</div>
  <div class="bar" style="left:452px;top:602px;width:196px">Physical Damage Deductible</div>
  <div class="check" style="left:58px;top:634px">Rejected</div>
  <div class="check" style="left:246px;top:634px">$500</div>
  <div class="check" style="left:292px;top:634px">$1,000</div>
  <div class="check" style="left:341px;top:634px">$2,500</div>
  <div class="check" style="left:392px;top:634px">$5,000</div>
  <div class="check" style="left:451px;top:634px">$500</div>
  <div class="check" style="left:497px;top:634px">$1,000</div>
  <div class="check" style="left:546px;top:634px">$2,500</div>
  <div class="check" style="left:595px;top:634px">$5,000</div>

  <div class="label" style="left:40px;top:657px">Driving radius</div>
  <div class="field" style="left:40px;top:672px;width:608px">Enter Your Text Here</div>
  <div class="label" style="left:42px;top:709px">How many years have you had your own continuous commercial auto insurance coverage for the current business name?</div>
  <div class="field" style="left:42px;top:727px;width:605px">Enter Your Text Here</div>

  <div class="bar" style="left:40px;top:766px;width:300px;height:24px">Do any of your vehicles travel across state lines?</div>
  <div class="field tall" style="left:352px;top:766px;width:296px;height:44px">If Yes</div>
  <div class="check" style="left:58px;top:800px">Yes</div>
  <div class="check" style="left:132px;top:800px">No</div>

  <div class="bar" style="left:40px;top:831px;width:608px;height:24px">What is the maximum radius traveled for your customer's business?</div>
  <div class="check" style="left:58px;top:871px">0-25 miles</div>
  <div class="check" style="left:133px;top:871px">26-50 miles</div>
  <div class="check" style="left:210px;top:871px">51-75 miles</div>
  <div class="check" style="left:289px;top:871px">76-100 miles</div>
  <div class="check" style="left:367px;top:871px">101-150 miles</div>
  <div class="check" style="left:442px;top:871px">151-200 miles</div>
  <div class="check" style="left:519px;top:871px">201-300 miles</div>
  <div class="check" style="left:597px;top:871px">300+ miles</div>

  <div class="label" style="left:40px;top:905px">Would you like physical damage coverage for this vehicle?</div>
  <div class="field select" style="left:40px;top:924px;width:410px">SAMPLE UTILITY VAN MODEL<svg viewBox="0 0 9 6"><path d="M1 1l3.5 3.5L8 1"/></svg></div>
  <div class="check" style="left:478px;top:931px">Yes</div>
  <div class="check" style="left:536px;top:931px">No</div>
</section>

<!-- Page 2: vehicles and drivers -->
<section class="page page-vehicles">
  <div class="brand"><span class="brand-mark"></span>RIDGEWAY<small>INSURANCE SERVICES</small></div>
  <div class="divider"></div>
  <div class="contact">
    <p><svg viewBox="0 0 10 12"><path d="M5 0a4 4 0 0 0-4 4c0 3 4 8 4 8s4-5 4-8a4 4 0 0 0-4-4zm0 5.6A1.6 1.6 0 1 1 5 2.4a1.6 1.6 0 0 1 0 3.2z"/></svg>Ridgeway Insurance Services</p>
    <p>4820 Maple Crest Ave Suite 110</p>
    <p class="gap">Riverton, CA 90817</p>
    <p><svg viewBox="0 0 12 12"><path d="M1 4c0-2 2-3 5-3s5 1 5 3l-2 1-1-2H4L3 5zM2.5 6h7l1 5h-9z"/></svg>Tel: (555) 310-2290</p>
  </div>

  <div class="band" style="top:116px">COMMERCIAL AUTO INSURANCE APPLICATION</div>
  <div class="caption" style="top:165px">VEHICLE INFORMATION</div>
  <div class="table vehicles" style="top:188px">
    <div class="thead"><span>Vin</span><span>Year</span><span>Make</span><span>Model</span><span>Type of Vehicle</span><span>Trailers</span><span>Value $</span></div>
    <div class="tbody">
      <div class="tr"></div><div class="tr"></div><div class="tr"></div><div class="tr"></div><div class="tr"></div>
      <div class="tr"></div><div class="tr"></div><div class="tr"></div><div class="tr"></div><div class="tr"></div>
      <div class="tr"></div><div class="tr"></div><div class="tr"></div><div class="tr"></div><div class="tr"></div>
      <div class="tr"></div><div class="tr"></div><div class="tr"></div><div class="tr"></div><div class="tr"></div>
    </div>
  </div>

  <div class="caption" style="top:562px">DRIVER INFORMATION</div>
  <div class="table drivers" style="top:585px">
    <div class="thead"><span>Name</span><span>DOB</span><span>DL#</span><span>DL State</span><span>Class of License</span><span>Married</span><span style="font-size:6px">Number of years<br>driving Similar Vehicle</span></div>
    <div class="tbody">
      <div class="tr"><span class="check yes">Yes</span><span class="check no">No</span></div>
      <div class="tr"><span class="check yes">Yes</span><span class="check no">No</span></div>
      <div class="tr"><span class="check yes">Yes</span><span class="check no">No</span></div>
      <div class="tr"><span class="check yes">Yes</span><span class="check no">No</span></div>
      <div class="tr"><span class="check yes">Yes</span><span class="check no">No</span></div>
      <div class="tr"><span class="check yes">Yes</span><span class="check no">No</span></div>
      <div class="tr"><span class="check yes">Yes</span><span class="check no">No</span></div>
      <div class="tr"><span class="check yes">Yes</span><span class="check no">No</span></div>
      <div class="tr"><span class="check yes">Yes</span><span class="check no">No</span></div>
      <div class="tr"><span class="check yes">Yes</span><span class="check no">No</span></div>
      <div class="tr"><span class="check yes">Yes</span><span class="check no">No</span></div>
      <div class="tr"><span class="check yes">Yes</span><span class="check no">No</span></div>
      <div class="tr"><span class="check yes">Yes</span><span class="check no">No</span></div>
      <div class="tr"><span class="check yes">Yes</span><span class="check no">No</span></div>
      <div class="tr"><span class="check yes">Yes</span><span class="check no">No</span></div>
      <div class="tr"><span class="check yes">Yes</span><span class="check no">No</span></div>
      <div class="tr"><span class="check yes">Yes</span><span class="check no">No</span></div>
      <div class="tr"><span class="check yes">Yes</span><span class="check no">No</span></div>
      <div class="tr"><span class="check yes">Yes</span><span class="check no">No</span></div>
      <div class="tr"><span class="check yes">Yes</span><span class="check no">No</span></div>
    </div>
  </div>
</section>

<!-- Page 3: commercial property -->
<section class="page page-property">
  <div class="brand"><span class="brand-mark"></span>RIDGEWAY<small>INSURANCE SERVICES</small></div>
  <div class="divider"></div>
  <div class="contact">
    <p><svg viewBox="0 0 10 12"><path d="M5 0a4 4 0 0 0-4 4c0 3 4 8 4 8s4-5 4-8a4 4 0 0 0-4-4zm0 5.6A1.6 1.6 0 1 1 5 2.4a1.6 1.6 0 0 1 0 3.2z"/></svg>Ridgeway Insurance Services</p>
    <p>4820 Maple Crest Ave Suite 110</p>
    <p class="gap">Riverton, CA 90817</p>
    <p><svg viewBox="0 0 12 12"><path d="M1 4c0-2 2-3 5-3s5 1 5 3l-2 1-1-2H4L3 5zM2.5 6h7l1 5h-9z"/></svg>Tel: (555) 310-2290</p>
  </div>

  <div class="band" style="top:138px">COMMERCIAL PROPERTY APPLICATION</div>
  <div class="label" style="left:40px;top:185px">Business Name</div>
  <div class="label" style="left:248px;top:184px">Building Address</div>
  <div class="label" style="left:452px;top:184px">Building Description</div>
  <div class="field" style="left:40px;top:200px;width:196px">Enter Your Text Here</div>
  <div class="field" style="left:246px;top:200px;width:196px">Enter Your Text Here</div>
  <div class="field" style="left:452px;top:200px;width:196px">Enter Your Text Here</div>

  <div class="label" style="left:42px;top:241px">Building Amount</div>
  <div class="field" style="left:42px;top:259px;width:605px">Enter Your Text Here</div>

  <div class="label" style="left:40px;top:305px">Business Personal Property Amount: $</div>
  <div class="check" style="left:185px;top:304px">Not Needed</div>
  <div class="label" style="left:248px;top:304px">Building Sq Ft</div>
  <div class="label" style="left:452px;top:304px">Total Area Sq Ft</div>
  <div class="field" style="left:40px;top:320px;width:196px">Enter Your Text Here</div>
  <div class="field" style="left:246px;top:320px;width:196px">Enter Your Text Here</div>
  <div class="field" style="left:452px;top:320px;width:196px">Enter Your Text Here</div>

  <div class="bar" style="left:40px;top:364px;width:608px">Building Construction Type</div>
  <div class="check" style="left:43px;top:396px">Wood Frame</div>
  <div class="check" style="left:120px;top:396px">Steel</div>
  <div class="check" style="left:172px;top:396px">Fire Resistive</div>
  <div class="check" style="left:248px;top:396px">Non-Combustible</div>
  <div class="check" style="left:339px;top:396px">Other</div>
  <div class="field" style="left:383px;top:391px;width:265px;height:21px">Enter Your Text Here</div>

  <div class="label" style="left:40px;top:430px"># of stories</div>
  <div class="label" style="left:246px;top:430px">Year Built</div>
  <div class="label" style="left:451px;top:430px">Wiring improvement year</div>
  <div class="field" style="left:40px;top:445px;width:196px">Enter Your Text Here</div>
  <div class="field" style="left:246px;top:445px;width:196px">Enter Your Text Here</div>
  <div class="field" style="left:451px;top:445px;width:196px">Enter Your Text Here</div>

  <div class="label" style="left:40px;top:493px">Roofing improvement year</div>
  <div class="label" style="left:246px;top:493px">Plumbing improvement year</div>
  <div class="label" style="left:451px;top:493px">Heating improvement year</div>
  <div class="field" style="left:40px;top:508px;width:196px">Enter Your Text Here</div>
  <div class="field" style="left:246px;top:508px;width:196px">Enter Your Text Here</div>
  <div class="field" style="left:451px;top:508px;width:196px">Enter Your Text Here</div>

  <div class="label" style="left:42px;top:557px">What is to the right of the building and distance</div>
  <div class="field" style="left:42px;top:575px;width:605px">Enter Your Text Here</div>
  <div class="label" style="left:42px;top:625px">What is to the left of the building and distance</div>
  <div class="field" style="left:42px;top:643px;width:605px">Enter Your Text Here</div>
  <div class="label" style="left:42px;top:692px">What is in front of the building and distance</div>
  <div class="field" style="left:42px;top:710px;width:605px">Enter Your Text Here</div>
  <div class="label" style="left:42px;top:760px">What is behind the building and distance</div>
  <div class="field" style="left:42px;top:778px;width:605px">Enter Your Text Here</div>

  <div class="label" style="left:42px;top:829px">Burglar alarm installation and serviced by</div>
  <div class="check" style="left:212px;top:829px">None</div>
  <div class="field" style="left:42px;top:847px;width:605px">Enter Your Text Here</div>

  <div class="bar" style="left:40px;top:893px;width:608px;height:23px">Does the premises have fire protection?</div>
  <div class="check" style="left:58px;top:932px">Sprinkler system</div>
  <div class="check" style="left:165px;top:932px">Fire detection</div>
  <div class="check" style="left:265px;top:932px">Other</div>
  <div class="field" style="left:306px;top:927px;width:264px;height:21px">Enter Your Text Here</div>
  <div class="check" style="left:610px;top:932px">None</div>
</section>

</body>
</html>
```